Counseling Practice Business Card

I need a professional looking business card incorporating my new logo that was just completed. Card needs to incorporate my name and title, description of my specialty, my address, my phone number, my fax number, my email and my website URL. I need to be able to choose design on/with different paper colors and textures.
I do not have a lot of business card ideas so I am open to anything but I want bold,sharp, clear card without additional designs other than my logo (see attached file info). I am open to different color backgrounds or paper colors including black. I do not like traditional brackets around area codes in phone number or dashes between numbers in phone number. Am open to other ways of presenting including periods between numbers as appropriate. I do not know enough to know what I like yet but I want card to coordinate and work together with my logo. My practice emphasizes natural mental health interventions so any use of color (with background paper color or the blue and green in my logo) that elicits nature is nice. In addition to black, any natural brown or wood looking background might be desirable also. Most of the offerings so far look very similar and boring.

Target Market(s)

Potential therapy clients and other professionals

Contact Information for Business Card

Card information:
Gerald M. Whitcombe, Ph.D.
Licensed Clinical Psychologist
Integrative Health Coach
4812 Marlowe Ridge Blvd SE
Suite 310
Duluth, GA 30096
(770) 415-2983 phone
(770) 581-4096 fax
drgeraldwhitcombe@quillmarsh.net
brightfernwellness.net

Font styles to use
Serif
Sans Serif
Other font styles liked:
• anything that you think looks crisp, clear and easily readable

Requirements
Must have
• Any color used should coordinate with my logo design (see attached files).
• Card should be printed horizontally so top and bottom are longest sides of rectangle.
• Background color or paper color should complement and highlight logo. Do not like a white background. black, grey, brown or any color my logo would blend well with.
Nice to have
• I would like designer to utilize color to highlight letters/name or phone-fax-web symbols.
• Bottom edge of card could be highlighted if appropriate to an idea.
Should not have
• I would NOT want the card to have a pure white background at all.
• No clear cards.
• Cards should be oriented with long sides on bottom and top, NOT sides. DO NOT LIKE THIS THIN TALL ORIENTATION.

```html
<!DOCTYPE html>
<html lang="en">
<head>
<meta charset="utf-8">
<title>Brightfern Wellness — Business Card</title>
<link rel="stylesheet" href="https://fonts.googleapis.com/css2?family=Roboto:wght@400;500;700&display=swap">
<style>
  :root {
    --backdrop: #1c1c1e;
    --card-dark: #161616;
    --card-light: #f3f1ea;
    --brand-blue: #1f73c1;
    --brand-green: #146b36;
    --ink: #3a3a3a;
  }
  * { box-sizing: border-box; margin: 0; padding: 0; }
  html, body {
    width: 1200px; height: 900px; overflow: hidden;
    background: var(--backdrop);
    font-family: "Roboto", Arial, sans-serif;
  }
  .canvas { position: relative; width: 1200px; height: 900px; }
  .card {
    position: absolute; width: 640px; height: 366px;
    box-shadow: 0 18px 40px rgba(0,0,0,.55);
    overflow: hidden;
  }
  .card-back {
    left: 340px; top: 50px;
    background: linear-gradient(135deg, #111 0%, var(--card-dark) 55%, #262626 100%);
    display: flex; align-items: center; justify-content: center;
  }
  .card-front { left: 220px; top: 470px; background: var(--card-light); }

  .brand-mark { display: flex; align-items: center; gap: 14px; }
  .brand-dot {
    width: 22px; height: 22px; border-radius: 50%;
    background: var(--brand-blue); flex: none;
  }
  .brand-name {
    font-weight: 500; color: var(--brand-blue);
    line-height: 1.05;
  }
  .card-back .brand-name { font-size: 48px; }
  .card-front .brand-mark { position: absolute; left: 40px; top: 118px; }
  .card-front .brand-name { font-size: 36px; }

  .divider {
    position: absolute; left: 332px; top: 70px;
    width: 3px; height: 200px; background: var(--brand-blue);
  }
  .details { position: absolute; left: 354px; top: 66px; width: 272px; color: var(--ink); }
  .person-name { font-size: 21px; font-weight: 700; color: var(--brand-blue); white-space: nowrap; }
  .person-title { font-size: 15px; font-weight: 500; line-height: 1.3; margin-top: 4px; }
  .address { font-size: 15px; font-weight: 500; line-height: 1.35; margin-top: 12px; }
  .contact-list { list-style: none; margin-top: 12px; font-size: 14.5px; font-weight: 500; line-height: 1.45; }
  .contact-list li { display: flex; align-items: center; gap: 8px; white-space: nowrap; }
  .contact-list svg { width: 12px; height: 12px; flex: none; }
  .web-domain { color: var(--brand-blue); }

  .edge-bands { position: absolute; left: 0; bottom: 0; width: 640px; height: 40px; }
</style>
</head>
<body>
<main class="canvas">
  <section class="card card-back" aria-label="Card back">
    <div class="brand-mark">
      <span class="brand-dot"></span>
      <span class="brand-name">Brightfern Wellness</span>
    </div>
  </section>

  <section class="card card-front" aria-label="Card front">
    <div class="brand-mark">
      <span class="brand-dot"></span>
      <span class="brand-name">Brightfern<br>Wellness</span>
    </div>

    <div class="divider"></div>

    <div class="details">
      <p class="person-name">Gerald M. Whitcombe, Ph.D.</p>
      <p class="person-title">Licensed Clinical Psychologist<br>Integrative Health Coach</p>
      <p class="address">4812 Marlowe Ridge Blvd SE<br>Suite 310 Duluth, GA 30096</p>
      <ul class="contact-list">
        <li>
          <svg viewBox="0 0 12 12" aria-hidden="true"><path d="M2.5 1 L4.5 1 L5 3.5 L3.8 4.4 Q4.8 6.8 7.6 8.2 L8.5 7 L11 7.5 L11 9.5 Q10.5 11 9 11 Q2 10 1 3 Q1 1.5 2.5 1Z" fill="var(--brand-blue)"/></svg>
          770.415.2983
        </li>
        <li>
          <svg viewBox="0 0 12 12" aria-hidden="true"><rect x="3" y="1" width="6" height="3" fill="var(--brand-blue)"/><rect x="1" y="4.5" width="10" height="4.5" rx="1" fill="var(--brand-blue)"/><rect x="3" y="8" width="6" height="3" fill="var(--brand-blue)"/></svg>
          770.581.4096
        </li>
        <li>
          <svg viewBox="0 0 12 12" aria-hidden="true"><rect x="1" y="2.5" width="10" height="7" fill="none" stroke="var(--brand-blue)" stroke-width="1.2"/><path d="M1 2.5 L6 6.5 L11 2.5" fill="none" stroke="var(--brand-blue)" stroke-width="1.2"/></svg>
          drgeraldwhitcombe@quillmarsh.net
        </li>
        <li>
          <svg viewBox="0 0 12 12" aria-hidden="true"><circle cx="6" cy="6" r="5" fill="none" stroke="var(--brand-blue)" stroke-width="1.1"/><ellipse cx="6" cy="6" rx="2.2" ry="5" fill="none" stroke="var(--brand-blue)" stroke-width="1"/><line x1="1" y1="6" x2="11" y2="6" stroke="var(--brand-blue)" stroke-width="1"/></svg>
          <span>www.<span class="web-domain">brightfernwellness</span>.net</span>
        </li>
      </ul>
    </div>

    <svg class="edge-bands" viewBox="0 0 640 40" aria-hidden="true">
      <polygon points="0,4 300,18 290,40 0,40" fill="var(--brand-blue)"/>
      <polygon points="306,20 640,22 640,40 294,40" fill="var(--brand-green)"/>
    </svg>
  </section>
</main>
</body>
</html>
```